Ophthalmologist Needs Celebrity Endorsed LASIK Poster Advertisement

Dr. Gerald P. Olsen, MD is an eye physician and surgeon in Kauai, Hawaii. He is the premier ophthalmologist on Kauai and is the only LASIK surgeon. LASIK is a vision correction surgery to help patients reduce or eliminate their dependence on glasses and contact lenses. He has performed hundreds of LASIK procedures and recently did the procedure on one of the actresses from the hit movie "Iron Orchard". She has provided us with content and the rights to produce advertisements using her celebrity endorsement of Dr. Olsen and the LASIK procedure. We need a poster advertisement that will be placed in the lobby of our office building (which receives a lot of foot traffic to other offices). This poster should be eye-catching to passerby, but also convey the LASIK message. Our intent is to generate interest in the procedure (people who wear glasses and contact lenses). The final design should communicate the premier image of our ophthalmology practice and generate interest in LASIK. More information on our practice and LASIK can be found at: www.olseneyecare.example.
Updates

Project Deadline Extended
Reason: I am still getting back to a few designers on their designs and would like to see the changes before I make a final decision. Thanks for your patience!

Target Market(s)

Men and women ages 25-45 who wear glasses or contact lenses

Industry/Entity Type

Building

Requirements
Must have
• The poster should have our company name (Olsen Eye Care) and logo (attached). It should also use at least one of the attached photos of the celebrity. It should also have the following endorsement verbatum:
"Mahalo Dr. Olsen and staff. I will never take my new eyesight for granted. I love it! Thanks for your care and love." Aloha and God Bless, Marta Delgado, "Pualei" Da Bad Girl

```html
<!DOCTYPE html>
<html lang="en">
<head>
<meta charset="utf-8">
<title>Olsen Eye Care – LASIK Poster</title>
<link rel="stylesheet" href="https://fonts.googleapis.com/css2?family=Lato:ital,wght@0,300;0,400;0,700;1,300&display=swap">
<style>
  :root {
    --poster-yellow: #f5d31c;
    --quote-blue: rgba(112, 190, 212, 0.9);
    --quote-tab: rgba(160, 214, 228, 0.92);
    --name-teal: #84b8b5;
    --name-gold: #f2d21e;
    --ink: #161616;
    --ink-soft: #22302f;
    --white: #ffffff;
  }
  * { margin: 0; padding: 0; box-sizing: border-box; }
  html, body { width: 800px; height: 1200px; overflow: hidden; background: var(--poster-yellow); }
  .poster {
    position: relative;
    width: 800px;
    height: 1200px;
    background: var(--poster-yellow);
    font-family: "Lato", sans-serif;
    overflow: hidden;
  }
  .celebrity-photo {
    position: absolute;
    left: 0; top: 0;
    width: 800px; height: 727px;
    background:
      radial-gradient(ellipse 220px 380px at 420px 470px, #1c1c1e 0%, #2a2a2c 60%, rgba(42,42,44,0) 100%),
      radial-gradient(ellipse 180px 420px at 700px 420px, #8a93a6 0%, rgba(138,147,166,0) 100%),
      linear-gradient(180deg, #6f8a74 0%, #9aa89a 30%, #b8b6a8 55%, #8f948c 100%);
  }
  .endorsement {
    position: absolute;
    left: 16px; top: 367px;
    width: 453px; height: 360px;
    background: var(--quote-blue);
  }
  .endorsement-tab {
    position: absolute;
    left: 0; top: 0;
    width: 420px; height: 34px;
    background: var(--quote-tab);
  }
  .endorsement-quote {
    position: absolute;
    left: 20px; top: 40px;
    width: 425px;
    font-weight: 300;
    font-style: italic;
    font-size: 33px;
    line-height: 47px;
    letter-spacing: -0.5px;
    color: var(--white);
  }
  .endorser {
    position: absolute;
    left: 16px; top: 727px;
    width: 453px; height: 133px;
    background: var(--name-teal);
    padding: 22px 0 0 20px;
  }
  .endorser-name {
    font-weight: 700;
    font-size: 29px;
    line-height: 40px;
    color: var(--name-gold);
  }
  .endorser-role {
    font-weight: 400;
    font-size: 29px;
    line-height: 40px;
    color: var(--ink-soft);
  }
  .tagline {
    position: absolute;
    left: 40px; top: 930px;
    font-weight: 400;
    font-size: 34px;
    line-height: 48px;
    color: var(--ink);
  }
  .brand {
    position: absolute;
    left: 520px; top: 760px;
    width: 260px;
    text-align: center;
  }
  .brand-mark { display: block; margin: 0 auto 24px; }
  .brand-name {
    font-weight: 400;
    font-size: 34px;
    color: var(--ink);
    white-space: nowrap;
  }
</style>
</head>
<body>
<main class="poster">
  <div class="celebrity-photo" role="img" aria-label="Photo of the actress walking outdoors in a black top, blurred beach crowd behind her"></div>

  <section class="endorsement">
    <div class="endorsement-tab"></div>
    <p class="endorsement-quote">"Mahalo Dr. Olsen and staff. I will never take my new eyesight for granted. I love it! Thanks for your care and love."</p>
  </section>

  <div class="endorser">
    <p class="endorser-name">Marta Delgado,</p>
    <p class="endorser-role">"Pualei" Da Bad Girl</p>
  </div>

  <p class="tagline">We don’t have to tell you<br>about our LASIK surgery.<br>You’ll see for your self</p>

  <div class="brand">
    <svg class="brand-mark" width="220" height="220" viewBox="0 0 220 220" aria-hidden="true">
      <circle cx="110" cy="110" r="104" fill="none" stroke="#161616" stroke-width="6"/>
    </svg>
    <p class="brand-name">Olsen Eye Care</p>
  </div>
</main>
</body>
</html>
```